Growing the Ironclad Young Contender:
A Family Playbook for Nurturing Bold, Grounded, and Resilient Daughters at Games and Beyond.
📘 Book Cover Design Brief – “Growing the Ironclad Young Contender”

Project Title:
Design a bold, inspiring book cover for a best-selling book titled:
Growing the Ironclad Young Contender
Subtitle: A Family Playbook for Nurturing Bold, Grounded, and Resilient Daughters at Games and Beyond

🎯 Audience:

Parents of female athletes ages 14–20 who want their daughters to build confidence, strength, resilience, and long-term success both in sports and in life.

This book should feel encouraging, empowering, and credible — NOT cheesy, childish, or overly academic.

📕 Design Tone & Style:

Powerful and professional — should feel like a best-selling book from a leading performance or parenting expert

Emotionally compelling — conveys hope, resilience, strength, and possibility

Visually modern and clean — avoid anything overly busy, cliché, or childish

Heroic/aspirational tone — think transformation, leadership, strong positioning

💡 Visual Direction / Ideas (Use as Inspiration, Not Limitation):

Strong, confident teenage female athlete imagery — adaptable beyond one specific sport

Symbolic visuals — e.g. athlete standing strong, on a starting line, looking bold into the future, silhouette, or power stance

Bold typography that feels clean and modern (e.g., Proxima Nova, Montserrat, Gotham, Bebas Neue, etc.)

A title that stands out clearly when viewed as a thumbnail on Brindlemart

Color tones: Empowering, modern, and strong: think deep blues, greens, purples, or golds — avoid playful pastels or overly girly themes

Potential imagery: textured backgrounds, motion, bravery, development, strength, growth, sport/action overlays

🔥 What the Cover MUST Communicate:

✅ This is for parents who want strong, confident female athletes
✅ It’s a guidebook for personal development AND sports performance
✅ It’s about creating “IRONCLAD” confidence — physically, mentally and emotionally
✅ The message is: You can help your daughter become her strongest, most confident self

📚 Back-of-Book Summary (for context):

"Growing the Ironclad Young Contender" is a parent's blueprint to building girls who are strong in body, confident in mind, and ready to lead on and off the field. Through simple strategies around strength training, mindset, nutrition, and character development, this book gives parents the tools to help their daughters stay injury-resistant, break through mental barriers, and unlock their full potential — in sports and in life.

✅ Deliverables:

Full cover design (front, back, spine) for paperback
High-resolution files (print-ready)
Source files (PSD, AI, etc.)
3D mockup versions of the book (standing, flat, stack)

Target Market(s)

Industry/Entity Type

Fitness

Font styles to use
Sans Serif

Colors
FFF300
FFF600
FEFA6F
FFFEC7
FFFEE8

Requirements
Must have
• Bold Font
Should not have
• I don't want an image of a female athlete. I want this to be font based.

```html
<!DOCTYPE html>
<html lang="en">
<head>
<meta charset="utf-8">
<title>Growing the Ironclad Young Contender</title>
<link href="https://fonts.googleapis.com/css2?family=Montserrat:wght@700;800;900&display=swap" rel="stylesheet">
<style>
  :root {
    --navy: #2d3f78;
    --navy-deep: #24346a;
    --gold-dark: #b39a4c;
    --gold-light: #ece3a6;
    --gold-mid: #d3c27c;
    --white: #ffffff;
  }
  html, body {
    margin: 0;
    padding: 0;
    width: 800px;
    height: 1200px;
    overflow: hidden;
    background: var(--navy);
  }
  .cover {
    position: relative;
    width: 800px;
    height: 1200px;
    overflow: hidden;
    background:
      radial-gradient(ellipse at 50% 45%, #324684 0%, var(--navy) 55%, var(--navy-deep) 100%);
    font-family: "Montserrat", sans-serif;
  }
  .cover-title {
    position: absolute;
    left: 0;
    top: 0;
    width: 800px;
    height: 460px;
  }
  .cover-title text {
    font-family: "Montserrat", sans-serif;
    font-weight: 900;
    fill: url(#gold-sheen);
  }
  .cover-art {
    position: absolute;
    left: 150px;
    top: 465px;
    width: 540px;
    height: 400px;
    border-radius: 50%;
    background: radial-gradient(ellipse at 45% 50%, rgba(211,186,90,0.55) 0%, rgba(211,186,90,0.2) 45%, rgba(45,63,120,0) 72%);
  }
  .cover-subtitle {
    position: absolute;
    left: 60px;
    top: 880px;
    width: 680px;
    margin: 0;
    text-align: center;
    color: var(--white);
    font-weight: 700;
    font-size: 22px;
    line-height: 31px;
    letter-spacing: 0.3px;
    text-transform: uppercase;
  }
  .publisher-mark {
    position: absolute;
    left: 0;
    top: 1070px;
    width: 800px;
    display: flex;
    flex-direction: column;
    align-items: center;
    gap: 12px;
  }
  .publisher-mark-circle {
    width: 80px;
    height: 80px;
    border-radius: 50%;
    border: 3px solid var(--gold-mid);
    box-sizing: border-box;
  }
  .publisher-mark-name {
    color: var(--white);
    font-weight: 800;
    font-size: 24px;
    letter-spacing: 1px;
  }
</style>
</head>
<body>
  <main class="cover">
    <svg class="cover-title" viewBox="0 0 800 460" role="heading" aria-level="1" aria-label="Growing the Ironclad Young Contender">
      <defs>
        <linearGradient id="gold-sheen" x1="75" y1="0" x2="728" y2="0" gradientUnits="userSpaceOnUse">
          <stop offset="0" stop-color="#b39a4c"/>
          <stop offset="0.5" stop-color="#ece3a6"/>
          <stop offset="1" stop-color="#b39a4c"/>
        </linearGradient>
      </defs>
      <text x="76" y="135" font-size="96" textLength="652" lengthAdjust="spacingAndGlyphs">GROWING THE</text>
      <text x="76" y="207" font-size="98" textLength="652" lengthAdjust="spacingAndGlyphs">IRONCLAD</text>
      <text x="76" y="329" font-size="156" textLength="652" lengthAdjust="spacingAndGlyphs">YOUNG</text>
      <text x="76" y="439" font-size="148" textLength="652" lengthAdjust="spacingAndGlyphs">CONTENDER</text>
    </svg>

    <div class="cover-art" role="img" aria-label="Gold line-drawn sprinter bursting forward with motion streaks"></div>

    <p class="cover-subtitle">A Family Playbook for Nurturing Bold,<br>Grounded, and Resilient Daughters<br>at Games and Beyond</p>

    <div class="publisher-mark">
      <div class="publisher-mark-circle"></div>
      <div class="publisher-mark-name">IRONCLAD</div>
    </div>
  </main>
</body>
</html>
```